Business cards for a fun web development agency

Hi,I am building a web development agency. You can read about it on the website http://kite-loft.examplehost.com. Basically, I want to focus on free and open source products and stay as far away from the corporate business feeling as possible. I want to build a community so I want the business card to feel fun and approachable (at the risk of professional if need be). I am uploading some of my image assets in various file formats. Feel free to use them or make your own if you want just keeping in theme with the website.
Industry/Entity Type
Building
Contact Information for Business Card
Company Name: Boat ShedWebsite: www.kiteloftdev.example (it's currently in alpha on http://kite-loft.examplehost.com if you want to see the them we are trying to capture)My name is: Banner B. SchaferMy email: banner@boatsheddev.comMy phone: 0431 587 904
Look and feel

```html
<!DOCTYPE html>
<html lang="en">
<head>
<meta charset="utf-8">
<title>Kite Loft — Business Cards</title>
<link rel="stylesheet" href="https://fonts.googleapis.com/css2?family=Arimo:wght@400;700&display=swap">
<style>
  :root {
    --brand-blue: #1481b0;
    --ink-navy: #2b4a73;
    --card-white: #ffffff;
    --backdrop: #e6e3e0;
    --card-shadow: rgba(60, 50, 40, 0.18);
  }
  * { box-sizing: border-box; margin: 0; padding: 0; }
  html, body {
    width: 1200px;
    height: 1189px;
    overflow: hidden;
    background: var(--backdrop);
    font-family: "Arimo", Arial, sans-serif;
  }
  .sheet {
    position: relative;
    width: 1200px;
    height: 1189px;
  }
  .card {
    position: absolute;
    left: 180px;
    width: 840px;
    height: 480px;
    background: var(--card-white);
    box-shadow: 0 10px 30px var(--card-shadow);
    overflow: hidden;
  }
  .card--front { top: 85px; }
  .card--back { top: 625px; }

  /* Front */
  .front-wordmark {
    position: absolute;
    inset: 0;
    display: flex;
    align-items: center;
    justify-content: center;
    gap: 22px;
  }
  .front-wordmark .mark-dot {
    width: 74px;
    height: 74px;
    border-radius: 50%;
    background: var(--brand-blue);
  }
  .front-wordmark .company-name {
    font-size: 78px;
    font-weight: 400;
    color: var(--brand-blue);
    letter-spacing: 1px;
  }

  /* Back */
  .back-brand {
    position: absolute;
    left: 60px;
    top: 120px;
    width: 300px;
    display: flex;
    flex-direction: column;
    align-items: center;
    gap: 18px;
  }
  .back-brand .mark-dot {
    width: 200px;
    height: 200px;
    border-radius: 50%;
    background: var(--brand-blue);
  }
  .back-brand .company-name {
    font-size: 30px;
    font-weight: 400;
    color: var(--brand-blue);
  }
  .divider {
    position: absolute;
    left: 400px;
    top: 95px;
    width: 2px;
    height: 260px;
    background: var(--ink-navy);
  }
  .holder-name {
    position: absolute;
    left: 440px;
    top: 110px;
    font-size: 36px;
    font-weight: 700;
    color: var(--brand-blue);
  }
  .contact-list {
    position: absolute;
    left: 440px;
    top: 220px;
    list-style: none;
    display: flex;
    flex-direction: column;
    gap: 10px;
  }
  .contact-item {
    display: flex;
    align-items: center;
    gap: 12px;
    font-size: 24px;
    color: var(--ink-navy);
  }
  .contact-icon {
    width: 24px;
    height: 24px;
    flex: none;
  }
  .accent-band {
    position: absolute;
    left: 0;
    right: 0;
    bottom: 55px;
    height: 40px;
    background: var(--brand-blue);
  }
</style>
</head>
<body>
<main class="sheet">

  <section class="card card--front" aria-label="Card front">
    <div class="front-wordmark">
      <span class="mark-dot" aria-hidden="true"></span>
      <span class="company-name">Kite Loft</span>
    </div>
  </section>

  <section class="card card--back" aria-label="Card back">
    <div class="back-brand">
      <span class="mark-dot" aria-hidden="true"></span>
      <span class="company-name">Kite Loft</span>
    </div>

    <div class="divider" aria-hidden="true"></div>

    <h1 class="holder-name">Corwin T. Aldous</h1>

    <ul class="contact-list">
      <li class="contact-item">
        <svg class="contact-icon" viewBox="0 0 24 24" aria-hidden="true">
          <rect width="24" height="24" rx="3" fill="#1481b0"/>
          <path d="M8 5.5l2 3-1.3 1.4c.8 1.8 2.3 3.3 4.1 4.1L14.2 12.7l3 2-1 2.5c-5.5-.3-9.6-4.4-9.9-9.9z" fill="#fff"/>
        </svg>
        <span>0431 587 904</span>
      </li>
      <li class="contact-item">
        <svg class="contact-icon" viewBox="0 0 24 24" aria-hidden="true">
          <rect width="24" height="24" rx="3" fill="#1481b0"/>
          <circle cx="12" cy="12" r="7" fill="none" stroke="#fff" stroke-width="1.5"/>
          <ellipse cx="12" cy="12" rx="3" ry="7" fill="none" stroke="#fff" stroke-width="1.2"/>
          <path d="M5 12h14" stroke="#fff" stroke-width="1.2"/>
        </svg>
        <span>www.kiteloftdev.example</span>
      </li>
      <li class="contact-item">
        <svg class="contact-icon" viewBox="0 0 24 24" aria-hidden="true">
          <rect width="24" height="24" rx="3" fill="#1481b0"/>
          <rect x="5" y="7" width="14" height="10" fill="none" stroke="#fff" stroke-width="1.5"/>
          <path d="M5 7l7 6 7-6" fill="none" stroke="#fff" stroke-width="1.5"/>
        </svg>
        <span>corwin@kiteloftdev.example</span>
      </li>
    </ul>

    <div class="accent-band" aria-hidden="true"></div>
  </section>

</main>
</body>
</html>
```